Redesign of business card for Cedar Ridge Mechanical

We are looking for a new design for our business cards for Cedar Ridge Mechanical. We are a plumbing & HVAC construction company, operating on the West Coast of Canada and USA. Logo attached.
Industry/Entity Type
Construction - Plumbing & HVAC
Contact Information for Business Card
Name, address, phone numbers, email, website address
Look and feel
Each slider illustrates characteristics of the customer's brand and the style your logo design should communicate.

```html
<!DOCTYPE html>
<html lang="en">
<head>
<meta charset="utf-8">
<title>Cedar Ridge Mechanical – Business Card</title>
<link rel="stylesheet" href="https://fonts.googleapis.com/css2?family=Figtree:wght@400;500;600;700&display=swap">
<style>
  :root {
    --page-bg: #d9d2c8;
    --card-bg: #ebe3d8;
    --card-edge: #f6f1ea;
    --ink: #1c1b1a;
    --ink-soft: #4a4743;
    --band: #6e6a64;
    --tab-bg: #1a1918;
    --tab-text: #e8dccb;
  }
  * { box-sizing: border-box; margin: 0; padding: 0; }
  html, body {
    width: 1200px; height: 1047px; overflow: hidden;
    background: var(--page-bg);
    font-family: "Figtree", sans-serif;
  }
  .business-card {
    position: absolute;
    left: 100px; top: 250px;
    width: 1000px; height: 547px;
    background: var(--card-bg);
    border: 2px solid var(--card-edge);
    border-radius: 22px;
    overflow: hidden;
    box-shadow: 0 10px 30px rgba(60, 50, 40, 0.18);
  }
  .brand {
    position: absolute;
    left: 60px; top: 200px;
    width: 440px;
    display: flex; align-items: center; justify-content: center; gap: 16px;
  }
  .brand-square {
    width: 26px; height: 26px;
    background: var(--ink);
    flex: none;
  }
  .brand-name {
    font-size: 30px; font-weight: 700;
    color: var(--ink);
    letter-spacing: 1px;
    text-transform: uppercase;
    white-space: nowrap;
  }
  .divider {
    position: absolute;
    left: 564px; top: 122px;
    width: 2px; height: 302px;
    background: var(--ink);
  }
  .contact {
    position: absolute;
    left: 590px; top: 112px;
    color: var(--ink-soft);
  }
  .contact-name {
    font-size: 31px; font-weight: 700;
    color: var(--ink);
    letter-spacing: 0.5px;
    line-height: 1.1;
  }
  .contact-title {
    font-size: 24px; font-weight: 400;
    margin-top: 8px;
  }
  .contact-address {
    font-size: 25px; font-weight: 500;
    color: var(--ink);
    line-height: 1.45;
    margin-top: 22px;
  }
  .contact-lines {
    list-style: none;
    margin-top: 20px;
  }
  .contact-lines li {
    display: flex; align-items: center; gap: 10px;
    font-size: 25px; font-weight: 500;
    color: var(--ink);
    line-height: 38px;
  }
  .contact-lines svg { width: 22px; height: 22px; flex: none; }
  .bottom-band {
    position: absolute;
    left: 0; bottom: 0;
    width: 660px; height: 14px;
    background: var(--band);
    opacity: 0.75;
  }
  .web-tab {
    position: absolute;
    right: 0; bottom: 0;
    width: 364px; height: 44px;
    background: var(--tab-bg);
    clip-path: polygon(26px 0, 100% 0, 100% 100%, 0 100%);
    display: flex; align-items: center; justify-content: center;
    padding-left: 22px;
    color: var(--tab-text);
    font-size: 23px; font-weight: 500;
  }
</style>
</head>
<body>
  <div class="business-card">
    <div class="brand">
      <span class="brand-square"></span>
      <span class="brand-name">Cedar Ridge Mechanical</span>
    </div>

    <div class="divider"></div>

    <div class="contact">
      <div class="contact-name">DANIEL HARPER</div>
      <div class="contact-title">Managing Director</div>
      <div class="contact-address">Your address, City<br>State, Zip 1234</div>
      <ul class="contact-lines">
        <li>
          <svg viewBox="0 0 24 24" aria-hidden="true"><path fill="#1c1b1a" d="M6.6 10.8a15.1 15.1 0 0 0 6.6 6.6l2.2-2.2a1 1 0 0 1 1-.25 11.4 11.4 0 0 0 3.6.57 1 1 0 0 1 1 1V20a1 1 0 0 1-1 1A17 17 0 0 1 3 4a1 1 0 0 1 1-1h3.5a1 1 0 0 1 1 1c0 1.25.2 2.45.57 3.6a1 1 0 0 1-.25 1z"/></svg>
          123 456 789
        </li>
        <li>
          <svg viewBox="0 0 24 24" aria-hidden="true"><rect x="6" y="2" width="12" height="20" rx="2" fill="none" stroke="#1c1b1a" stroke-width="2"/><circle cx="12" cy="18" r="1.2" fill="#1c1b1a"/></svg>
          123 456 789
        </li>
        <li>
          <svg viewBox="0 0 24 24" aria-hidden="true"><rect x="2" y="5" width="20" height="14" rx="2" fill="#1c1b1a"/><path d="M3 6l9 7 9-7" fill="none" stroke="#ebe3d8" stroke-width="1.6"/></svg>
          info@cedarridgemech.com
        </li>
      </ul>
    </div>

    <div class="bottom-band"></div>
    <div class="web-tab">www.cedarridgemech.com</div>
  </div>
</body>
</html>
```